Website for Vornelix Capital, my new firm that raises money from investors to buy, build, own an...

Vornelix Capital needs a website! We are a new company with very experienced people, who invest in, own and build hotel properties, as well as apartments and other commercial real estate. We seek investors for our projects, and we provide safe, secure returns on their investment in our projects. Our new logo is designed to exhibit strength, class and security, and would like our website to continue on this theme. Our name, Vornelix, is a word-play on a Greek word “aristeia”, which means “excellence” and “a warriors finest moment of glory in war”. If you are in business, you realize that much of it is like war, with strategy and moves and opponents and competitors, and ever-changing economic conditions and threats that make business very much like war. We like to think that we are good at business (war), and so have named our company “Vornelix”, using the founders last name and the word “aristeia” combined. Another definition of "aristeia" is "performing at the peak of one's potential after a long struggle"...again, much like business in real life! The website design should exhibit financial security, smart moves, and positive growth towards a bright future.

Target Market(s)

The target market is smart and wealthy investors, with others such as brokers, cities and government agencies, lenders, sellers, partners, etc also looking at it.

Industry/Entity Type

Investment

Number of Pages Required

5+ page

Font styles to use
Sans Serif

Colors
fec214

Requirements
Must have
• Our website should have a landing page, a "about" or bio page, a projects page and a contact us page. Our new logo uses the colors black and gold, so this should be factored in to our site. The site should be simple, yet impactful and impressive. I have actually two logos, which can be mixed and interchanged in a complimentary way, each with their own unique look.
Nice to have
• I have uploaded a couple screenshots of a website i like, and the simplicity I mention.
Should not have
• The site should not be flashy or complicated or complex or "busy"

```html
<!DOCTYPE html>
<html lang="en">
<head>
<meta charset="utf-8">
<title>Vornelix Capital</title>
<link href="https://fonts.googleapis.com/css2?family=Montserrat:wght@400;500;600&display=swap" rel="stylesheet">
<style>
:root{
  --gold:#fec214;
  --gold-deep:#f2b31a;
  --ink:#2b2b2b;
  --dark:#141414;
  --muted:#555;
  --paper:#f5f5f5;
  --white:#fff;
}
*{margin:0;padding:0;box-sizing:border-box}
html,body{width:1200px;height:2314px;overflow:hidden}
body{font-family:Arial,Helvetica,sans-serif;color:var(--ink);background:var(--white);position:relative}
.head{font-family:"Montserrat",Arial,sans-serif}
section,footer{position:absolute;left:0;width:1200px}

/* hero */
.hero{top:0;height:637px;background:linear-gradient(100deg,#d4ebf8 0%,#eaf4fa 45%,#f7f9fb 100%)}
.hero-art{position:absolute;left:640px;top:95px;width:560px;height:542px;background:linear-gradient(180deg,rgba(220,224,230,.2),rgba(200,205,212,.8))}
.brand{position:absolute;left:86px;top:40px;font-family:"Montserrat",Arial,sans-serif;font-weight:600;font-size:20px;line-height:26px;color:var(--ink);letter-spacing:1px;text-transform:uppercase;text-align:center}
.nav{position:absolute;top:58px;left:0;width:1200px;font-family:"Montserrat",Arial,sans-serif;font-weight:600;font-size:13px;color:var(--ink)}
.nav a{position:absolute;text-decoration:none;color:inherit}
.nav .active{color:var(--gold-deep)}
.hero h1{position:absolute;left:86px;top:255px;font-family:"Montserrat",Arial,sans-serif;font-weight:500;font-size:39px;color:#333;letter-spacing:.5px}
.hero .tagline{position:absolute;left:86px;top:319px;font-family:"Montserrat",Arial,sans-serif;font-weight:600;font-size:12.5px;color:var(--gold-deep)}
.hero .intro{position:absolute;left:86px;top:348px;width:450px;font-size:13px;line-height:26.5px;color:#444}
.btn-outline{position:absolute;display:flex;align-items:center;justify-content:center;border-radius:30px;font-family:"Montserrat",Arial,sans-serif;font-weight:500;text-transform:uppercase}
.hero .btn-outline{left:88px;top:451px;width:148px;height:48px;border:1.5px solid #888;color:#555;font-size:14px}

/* bio */
.bio{top:637px;height:542px;background:radial-gradient(ellipse at 50% 30%,#5a5a5a 0%,#333 45%,#1d1d1d 100%);color:var(--white);text-align:center}
.section-title{position:absolute;left:0;width:1200px;text-align:center;font-family:"Montserrat",Arial,sans-serif;font-weight:500;text-transform:uppercase}
.rule{position:absolute;left:565px;width:72px;height:2px;background:var(--gold)}
.bio .section-title{top:110px;font-size:46px}
.bio .rule{top:180px}
.bio p{position:absolute;left:300px;top:208px;width:600px;font-size:13px;line-height:30px;color:#eee}
.bio .btn-outline{left:469px;top:386px;width:264px;height:54px;border:1.5px solid #ddd;color:var(--white);font-size:14px}

/* projects */
.projects{top:1179px;height:486px;background:var(--paper)}
.projects .section-title{top:36px;font-size:38px;color:#333}
.projects .rule{top:90px}
.card{position:absolute;top:119px;width:331px;height:311px;background:var(--white);box-shadow:0 1px 4px rgba(0,0,0,.15);text-align:center}
.card .photo{height:236px}
.card h3{font-family:"Montserrat",Arial,sans-serif;font-weight:500;font-size:17px;margin-top:19px;color:#333}
.card a{display:block;margin-top:6px;font-size:13px;color:var(--gold-deep)}
.photo-apartments{background:linear-gradient(160deg,#7aa8d8 0%,#c9a56a 55%,#5d5a3c 100%)}
.photo-commercial{background:linear-gradient(100deg,#2d3f52 0%,#9a4e22 35%,#c6cfd6 70%,#8fa0ad 100%)}
.photo-estate{background:linear-gradient(180deg,#5e7d9e 0%,#45506a 55%,#b8b6b0 100%)}

/* contact */
.contact{top:1665px;height:352px;background:linear-gradient(180deg,#fbbd1e 0%,#f3b52a 60%,#e5a82c 100%)}
.contact .section-title{top:40px;font-size:38px;color:var(--white)}
.contact .rule{top:93px;background:var(--white)}
.field{position:absolute;background:var(--white);font-size:13px;color:#666;padding:13px 14px}
.submit{position:absolute;left:518px;top:271px;width:164px;height:45px;background:#3a3a3a;color:var(--white);display:flex;align-items:center;justify-content:center;font-family:"Montserrat",Arial,sans-serif;font-weight:600;font-size:15px}

/* footer */
.footer{top:2017px;height:297px;background:var(--dark);color:var(--white);text-align:center}
.footer .brand{position:absolute;left:0;top:52px;width:1200px;color:var(--white);font-size:24px;line-height:30px}
.footer .divider{position:absolute;left:85px;top:135px;width:1025px;height:1px;background:#333}
.social{position:absolute;top:159px;width:58px;height:58px;border:1.5px solid #ccc;border-radius:50%;display:flex;align-items:center;justify-content:center;font-family:"Montserrat",Arial,sans-serif;font-weight:600;font-size:12px;color:var(--white)}
.copyright{position:absolute;left:0;top:249px;width:1200px;font-size:13px;color:#ddd}
</style>
</head>
<body>

<section class="hero">
  <div class="hero-art" role="img" aria-label="Line drawing of city skyscrapers"></div>
  <div class="brand">Vornelix<br>Capital</div>
  <nav class="nav">
    <a class="active" style="left:743px">[&nbsp; HOME &nbsp;]</a>
    <a style="left:844px">ABOUT</a>
    <a style="left:939px">PROJECTS</a>
    <a style="left:1054px">CONTACT</a>
  </nav>
  <h1>VORNELIX CAPITAL</h1>
  <div class="tagline">SED UT PERSPICIATIS UNDE OMNIS ISTE NATUS ERROR SIT VOLUPTATEM</div>
  <p class="intro">Nemo enim ipsam voluptatem quia voluptas sit aspernatur aut odit aut fugit, sed quia consequuntur magni dolores eos qui ratione voluptatem sequi nesciunt. Neque velit- sed quia non numquam eius modi tempora....</p>
  <div class="btn-outline">Read More</div>
</section>

<section class="bio" role="img" aria-label="Businessman overlooking a city skyline, darkened">
  <h2 class="section-title">Our Bio</h2>
  <div class="rule"></div>
  <p>Sed ut perspiciatis unde omnis iste natus error sit voluptatem accusantium doloremque laudantium, totam rem aperiam, eaque ipsa quae ab illo inventore veritatis et quasi architecto beatae vitae dicta sunt explicabo Nemo enim ipsam voluptatem quia voluptas sit aspernatur aut odit aut fugit, sed quia consequuntur magni dolorese os qui ratione voluptatem sequi nesciunt.Neque porro quisquam est, qui dolorem ipsum quia dolor sit amet, consectetur, adipisci velit, sed quia non numquam eius modi tempora</p>
  <div class="btn-outline">Click Here For More Info</div>
</section>

<section class="projects">
  <h2 class="section-title">Our Projects</h2>
  <div class="rule"></div>
  <div class="card" style="left:86px">
    <div class="photo photo-apartments" role="img" aria-label="Apartment building at sunset"></div>
    <h3>APARTMENTS</h3>
    <a>Click Here For More Info</a>
  </div>
  <div class="card" style="left:435px">
    <div class="photo photo-commercial" role="img" aria-label="Glass-walled commercial interior"></div>
    <h3>COMMERCIAL</h3>
    <a>Click Here For More Info</a>
  </div>
  <div class="card" style="left:782px">
    <div class="photo photo-estate" role="img" aria-label="Modern family house at dusk"></div>
    <h3>REAL ESTATE</h3>
    <a>Click Here For More Info</a>
  </div>
</section>

<section class="contact">
  <h2 class="section-title">Contact Us</h2>
  <div class="rule"></div>
  <div class="field" style="left:140px;top:120px;width:304px;height:44px">Name :</div>
  <div class="field" style="left:449px;top:120px;width:302px;height:44px">Email :</div>
  <div class="field" style="left:756px;top:120px;width:304px;height:44px">Phone :</div>
  <div class="field" style="left:140px;top:173px;width:922px;height:77px">Message :</div>
  <div class="submit">SUBMIT</div>
</section>

<footer class="footer">
  <div class="brand">Vornelix<br>Capital</div>
  <div class="divider"></div>
  <div class="social" style="left:386px">FB</div>
  <div class="social" style="left:460px">TW</div>
  <div class="social" style="left:530px">GP</div>
  <div class="social" style="left:604px">IN</div>
  <div class="social" style="left:673px">IG</div>
  <div class="social" style="left:746px">
    <svg width="18" height="14" viewBox="0 0 18 14" fill="none" stroke="#fff" stroke-width="1.5"><rect x="1" y="1" width="16" height="12"/><path d="M1 1l8 7 8-7"/></svg>
  </div>
  <div class="copyright">© Copyrights 2018 - Vornelix Capital.All Rights Reserved.</div>
</footer>

</body>
</html>
```